I want a website to be designed for our new company, it's an import and export company for variety of things.

please see the attached Logo for our company and the Images for our different sections for our busienss

Target Market(s)

multiple

Coding

Coded - Design and coding required

Number of Pages Required

5+ page

Font styles to use
Sans Serif

Colors

Designer to choose colors to be used in the design.

Requirements
Must have
• KVR GLOBALINKS
• KVR globalinks Trading & Contracting provides various services. The Company offers infrastructure construction, oil, enegy and gas services, agricultural projects, real estate development, travel and tourism, and food processing and trading.
• Civil contracting for infrastructure, residential and heavy projects. Through its main subsidiaries; distribution of general food products, construction chemicals including corrosion inhibitors and electrical machinery; provides catering and travel agency services; ownership and operation of a school; offers human sources services including manpower supply.
• Drilling and Gold Mines Used Machinery, All Kinds of Construction Machinery, Drilling Machines are manufactured and sold.
Nice to have
• good designa and beautiful colours, it has too look professional

```html
<!DOCTYPE html>
<html lang="en">
<head>
<meta charset="utf-8">
<title>KVR Globalinks</title>
<link href="https://fonts.googleapis.com/css2?family=Raleway:wght@300;400;500;600;700;800&family=Lora:wght@400&display=swap" rel="stylesheet">
<style>
:root{
  --orange:#f7901e;
  --dark:#262626;
  --darker:#1f1f1f;
  --ink:#2b2b2b;
  --grey:#6e6e6e;
  --light:#bdbdbd;
  --white:#ffffff;
}
*{margin:0;padding:0;box-sizing:border-box}
html,body{width:1200px;height:4334px;overflow:hidden}
body{position:relative;font-family:"Raleway",sans-serif;color:var(--ink);background:var(--white)}
.abs{position:absolute}
.photo{position:absolute}
.btn{position:absolute;display:flex;align-items:center;gap:8px;padding:0 10px;height:30px;font-size:11px;font-weight:600;letter-spacing:.3px;color:var(--white);background:var(--orange);text-transform:uppercase}
.btn .dot{width:16px;height:16px;border-radius:50%;background:var(--white);display:flex;align-items:center;justify-content:center}
.btn.dark{background:#2e2e2e}
.btn.dark .dot{background:var(--orange)}
.btn.dark .dot svg path{stroke:var(--white)}
.eyebrow{font-weight:300;color:var(--orange);font-size:24px}
.section-title{font-weight:700;font-size:42px;letter-spacing:.3px}
/* hero */
.sidebar{position:absolute;left:0;top:0;width:295px;height:598px}
.brand{position:absolute;left:93px;top:48px;width:160px;display:flex;flex-direction:column;align-items:center;gap:10px;color:var(--white)}
.brand .mark{width:34px;height:34px;border-radius:50%;background:var(--orange)}
.brand .name{font-size:15px;font-weight:600;letter-spacing:2px}
.nav{position:absolute;left:93px;top:170px;width:148px;list-style:none}
.nav li{height:56px;border-bottom:1px solid #3c3c3c;font-family:"Lora",serif;font-size:12px;color:#cfcfcf;display:flex;align-items:center;padding-left:6px}
.nav li.active{color:var(--white);border-left:2px solid var(--orange);padding-left:6px;height:36px;margin:10px 0 10px 0}
.follow{position:absolute;left:93px;top:466px;font-family:"Lora",serif;font-size:15px;color:var(--white)}
.socials{position:absolute;display:flex;gap:8px}
.socials span{width:26px;height:26px;border-radius:50%;background:var(--white)}
.socials span.on{background:var(--orange)}
.hero-title{position:absolute;left:321px;top:328px;font-weight:700;font-size:60px;line-height:64px;color:var(--white)}
.hero-title .accent{color:var(--orange)}
.hero-sub{position:absolute;left:321px;top:455px;font-size:22px;font-weight:500;color:var(--white)}
/* welcome */
.para{font-size:13.5px;line-height:22.6px;color:var(--grey)}
/* services */
.band{position:absolute;left:0;width:1200px;background:var(--dark)}
.center{position:absolute;left:0;width:1200px;text-align:center}
.card{position:absolute;width:241px}
.card .pic{height:157px}
.card .cat{margin-top:10px;font-size:14px;color:#d4d4d4}
.card .title{font-size:21px;font-weight:500;color:var(--white);margin-top:2px}
.card .text{margin-top:8px;font-size:11px;line-height:18px;color:#a9a9a9}
.card .btn{position:relative;margin-top:14px;display:inline-flex}
.view-all{position:absolute;left:515px;top:2148px;width:168px;height:32px;background:var(--white);font-size:11px;font-weight:600;display:flex;align-items:center;justify-content:center;color:var(--ink)}
/* news */
.news{position:absolute;width:324px}
.news .pic{height:201px}
.news .title{margin-top:22px;font-size:18.5px;line-height:27px;color:var(--white)}
.news .text{margin-top:12px;font-size:11px;line-height:19.5px;color:#a9a9a9}
.news .btn{position:relative;margin-top:18px;display:inline-flex}
/* footer */
.f-head{position:absolute;top:3978px;font-size:19px;color:var(--ink)}
.f-list{position:absolute;list-style:none;font-size:11.5px;color:var(--grey)}
.f-list li{height:29px}
.f-list li::before{content:"•";color:var(--orange);margin-right:3px}
.contact{position:absolute;left:634px;font-size:11.5px;color:var(--grey);display:flex;gap:8px;line-height:16px}
.input{position:absolute;left:863px;width:242px;height:29px;border:1px solid #d6d6d6;font-size:9.5px;color:#999;padding-left:10px;display:flex;align-items:center}
.subscribe{position:absolute;left:863px;top:4093px;width:242px;height:29px;background:var(--orange);color:var(--white);font-size:12px;display:flex;align-items:center;justify-content:center}
.copyright{position:absolute;left:0;top:4185px;width:1200px;text-align:center;font-size:12.5px;color:var(--grey);letter-spacing:.3px}
.copyright b{color:var(--ink);font-weight:600}
.f-social{position:absolute;left:532px;top:4218px;display:flex;gap:8px}
.f-social span{width:28px;height:28px;border-radius:50%;border:1px solid #cfcfcf}
.f-social span.on{background:var(--darker);border-color:var(--darker)}
</style>
</head>
<body>

<!-- HERO -->
<svg class="abs" style="left:0;top:0" width="1200" height="600" aria-hidden="true">
  <defs>
    <linearGradient id="heroSky" x1="0" y1="0" x2="0" y2="1">
      <stop offset="0" stop-color="#6d6f72"/>
      <stop offset=".4" stop-color="#56604f"/>
      <stop offset=".75" stop-color="#8a7a5c"/>
      <stop offset="1" stop-color="#a58f6c"/>
    </linearGradient>
  </defs>
  <polygon points="295,0 1200,0 1200,598 295,556" fill="url(#heroSky)"/>
  <polygon points="0,0 295,0 295,598 0,539" fill="#262626"/>
</svg>
<div class="photo" role="img" aria-label="Open-pit mine in a mountain valley under a cloudy sky" style="left:295px;top:0;width:905px;height:556px;background:transparent"></div>

<div class="sidebar">
  <div class="brand"><span class="mark"></span><span class="name">KVR GLOBALINKS</span></div>
  <ul class="nav">
    <li class="active">Home</li>
    <li>About Us</li>
    <li>Services</li>
    <li>News</li>
    <li>Contact Us</li>
  </ul>
  <div class="follow">Follow Us On</div>
  <div class="socials" style="left:93px;top:505px"><span class="on"></span><span></span><span></span><span></span></div>
</div>

<div class="hero-title"><span class="accent">KVR</span><br>Globalinks</div>
<div class="hero-sub">A Large Assortment</div>

<!-- WELCOME -->
<svg class="abs" style="left:636px;top:685px" width="564" height="370" aria-hidden="true">
  <polygon points="0,0 564,28 564,370 0,370" fill="var(--orange)"/>
</svg>
<div class="photo" role="img" aria-label="Two engineers in hard hats shaking hands on a site" style="left:714px;top:744px;width:392px;height:380px;background:linear-gradient(135deg,#5c5b57,#8d8d88 45%,#d58a2c 70%,#3d4450)"></div>

<div class="abs eyebrow" style="left:93px;top:730px">Welcome To</div>
<div class="abs section-title" style="left:93px;top:758px">KVR GLOBALINKS</div>
<p class="abs para" style="left:93px;top:820px;width:510px">Sed ut perspiciatis unde omnis iste natus error sit voluptatem accusantium doloremque laudantium, totam rem aperiam, eaque ipsa quae ab illo inventore veritatis et quasi architecto beatae vitae dicta sunt explicabo. Nemo enim ipsam voluptatem quia voluptas sit aspernatur aut odit aut fugit, sed quia consequuntur magni dolores eos qui ratione voluptatem sequi nesciunt. Neque porro quisquam est, qui dolorem ipsum quia dolor sit amet, consectetur, adipisci velit, sed quia non numquam eius modi tempora incidunt ut labore et dolore magnam aliquam quaerat voluptatem.</p>
<div class="btn dark" style="left:93px;top:1042px">Read More <span class="dot"><svg width="8" height="8" viewBox="0 0 8 8"><path d="M3 1l3 3-3 3" fill="none" stroke="#f7901e" stroke-width="1.5"/></svg></span></div>

<!-- SERVICES -->
<div class="band" style="top:1212px;height:1038px"></div>
<div class="center eyebrow" style="top:1274px">KVR globalinks</div>
<div class="center section-title" style="top:1302px;color:var(--white)">OUR SERVICES</div>
<div class="center" style="top:1356px;font-size:15.5px;color:#d8d8d8">KVR globalinks Trading &amp; Contracting provides various services</div>

<div class="card" style="left:93px;top:1422px"><div class="pic" role="img" aria-label="Excavator on a construction site" style="background:linear-gradient(180deg,#4f8ccc,#9cc0e0 55%,#c98a52)"></div><div class="cat">Infrastructure</div><div class="title">Construction</div><div class="text">But I must explain to you how all this mistaken idea of denouncing pleasure and praising pain...</div><div class="btn">Read More <span class="dot"><svg width="8" height="8" viewBox="0 0 8 8"><path d="M3 1l3 3-3 3" fill="none" stroke="#222" stroke-width="1.5"/></svg></span></div></div>
<div class="card" style="left:350px;top:1422px"><div class="pic" role="img" aria-label="Gas refinery towers" style="background:linear-gradient(180deg,#2f6fd0,#6e9ee0 50%,#3b3b3b)"></div><div class="cat">Enegy and</div><div class="title">Gas Services</div><div class="text">But I must explain to you how all this mistaken idea of denouncing pleasure and praising pain...</div><div class="btn">Read More <span class="dot"><svg width="8" height="8" viewBox="0 0 8 8"><path d="M3 1l3 3-3 3" fill="none" stroke="#222" stroke-width="1.5"/></svg></span></div></div>
<div class="card" style="left:608px;top:1422px"><div class="pic" role="img" aria-label="Combine harvester and tractor in a field" style="background:linear-gradient(180deg,#c9ccd0,#8a8b76 55%,#5d6a3a)"></div><div class="cat">Agricultural</div><div class="title">Projects</div><div class="text">But I must explain to you how all this mistaken idea of denouncing pleasure and praising pain...</div><div class="btn">Read More <span class="dot"><svg width="8" height="8" viewBox="0 0 8 8"><path d="M3 1l3 3-3 3" fill="none" stroke="#222" stroke-width="1.5"/></svg></span></div></div>
<div class="card" style="left:865px;top:1422px"><div class="pic" role="img" aria-label="Tower crane over a building under construction" style="background:linear-gradient(180deg,#3f86d6,#86b6e6 60%,#8a5b3c)"></div><div class="cat">Real Estate</div><div class="title">Development</div><div class="text">But I must explain to you how all this mistaken idea of denouncing pleasure and praising pain...</div><div class="btn">Read More <span class="dot"><svg width="8" height="8" viewBox="0 0 8 8"><path d="M3 1l3 3-3 3" fill="none" stroke="#222" stroke-width="1.5"/></svg></span></div></div>

<div class="card" style="left:93px;top:1772px"><div class="pic" role="img" aria-label="Traveller with a suitcase in an airport terminal" style="background:linear-gradient(135deg,#e9e3cf,#9aa394 50%,#3c4046)"></div><div class="cat">Travel and</div><div class="title">Tourism</div><div class="text">But I must explain to you how all this mistaken idea of denouncing pleasure and praising pain...</div><div class="btn">Read More <span class="dot"><svg width="8" height="8" viewBox="0 0 8 8"><path d="M3 1l3 3-3 3" fill="none" stroke="#222" stroke-width="1.5"/></svg></span></div></div>
<div class="card" style="left:350px;top:1772px"><div class="pic" role="img" aria-label="Potatoes on a processing line" style="background:linear-gradient(135deg,#c9ad82,#8a6f4c 55%,#2f2d2b)"></div><div class="cat">Food</div><div class="title">Processing</div><div class="text">But I must explain to you how all this mistaken idea of denouncing pleasure and praising pain...</div><div class="btn">Read More <span class="dot"><svg width="8" height="8" viewBox="0 0 8 8"><path d="M3 1l3 3-3 3" fill="none" stroke="#222" stroke-width="1.5"/></svg></span></div></div>
<div class="card" style="left:608px;top:1772px"><div class="pic" role="img" aria-label="Offshore oil platform at sunset" style="background:linear-gradient(180deg,#e9a35c,#c97a4a 45%,#3d4d63)"></div><div class="cat">Oil</div><div class="title">Industries</div><div class="text">But I must explain to you how all this mistaken idea of denouncing pleasure and praising pain...</div><div class="btn">Read More <span class="dot"><svg width="8" height="8" viewBox="0 0 8 8"><path d="M3 1l3 3-3 3" fill="none" stroke="#222" stroke-width="1.5"/></svg></span></div></div>
<div class="card" style="left:865px;top:1772px"><div class="pic" role="img" aria-label="Group of workers in yellow hard hats" style="background:linear-gradient(180deg,#9ba3a8,#5c6166 50%,#2e3235)"></div><div class="cat">Human</div><div class="title">Sources Services</div><div class="text">But I must explain to you how all this mistaken idea of denouncing pleasure and praising pain...</div><div class="btn">Read More <span class="dot"><svg width="8" height="8" viewBox="0 0 8 8"><path d="M3 1l3 3-3 3" fill="none" stroke="#222" stroke-width="1.5"/></svg></span></div></div>

<div class="view-all">VIEW ALL SERVICES</div>

<!-- USED MACHINERY -->
<div class="abs" style="left:0;top:2336px;width:560px;height:337px;background:var(--orange)"></div>
<div class="photo" role="img" aria-label="Haul trucks working in a dusty gold mine" style="left:74px;top:2395px;width:392px;height:461px;background:linear-gradient(170deg,#efe3bf,#cdb57d 45%,#8d6b35)"></div>
<div class="photo" role="img" aria-label="Mining cart in an underground tunnel" style="left:473px;top:2701px;width:207px;height:155px;background:linear-gradient(135deg,#7a6a52,#4a3f33 60%,#2a2520)"></div>
<div class="photo" role="img" aria-label="Drilling machine inside a mine shaft" style="left:687px;top:2701px;width:205px;height:155px;background:linear-gradient(135deg,#4e5a6a,#2d3440 60%,#8a8c90)"></div>
<div class="photo" role="img" aria-label="Excavator at an open forest mining site" style="left:899px;top:2701px;width:207px;height:155px;background:linear-gradient(180deg,#8fa08a,#5f6e3e 45%,#a5754a)"></div>

<div class="abs eyebrow" style="left:601px;top:2330px">Drilling and Gold Mines</div>
<div class="abs section-title" style="left:601px;top:2358px">USED MACHINERY</div>
<div class="abs" style="left:601px;top:2414px;width:505px;font-size:16.5px;font-weight:700;line-height:23px">All Kinds of Construction Machinery, Drilling Machines are manufactured and sold.</div>
<p class="abs para" style="left:601px;top:2475px;width:508px">Sed ut perspiciatis unde omnis iste natus error sit voluptatem accusantium doloremque laudantium, totam rem aperiam, eaque ipsa quae ab illo inventore veritatis et quasi architecto beatae vitae dicta sunt explicabo. Nemo enim ipsam voluptatem quia voluptas sit aspernatur aut odit aut fugit, sed quia consequuntur magni dolores eos qui ratione voluptatem sequi nesciunt. Neque porro quisquam est, qui dolorem ipsum</p>
<div class="btn dark" style="left:601px;top:2641px">Read More <span class="dot"><svg width="8" height="8" viewBox="0 0 8 8"><path d="M3 1l3 3-3 3" fill="none" stroke="#f7901e" stroke-width="1.5"/></svg></span></div>

<!-- NEWS -->
<div class="band" style="top:2944px;height:599px"></div>
<div class="center eyebrow" style="top:3003px">KVR globalinks</div>
<div class="center section-title" style="top:3030px;color:var(--white)">LATEST NEWS</div>

<div class="news" style="left:93px;top:3098px"><div class="pic" role="img" aria-label="Business meeting at a table" style="background:linear-gradient(135deg,#b98a55,#7a5636 50%,#e3d7c6)"></div><div class="title">There are many variations passages Lorem Ipsum</div><div class="text">If you use this site regularly and would like to help keep the site on the Internet, please consider donating a small sum to help pay</div><div class="btn">Read More <span class="dot"><svg width="8" height="8" viewBox="0 0 8 8"><path d="M3 1l3 3-3 3" fill="none" stroke="#222" stroke-width="1.5"/></svg></span></div></div>
<div class="news" style="left:438px;top:3098px"><div class="pic" role="img" aria-label="Laptops and coffee cups on a meeting table" style="background:linear-gradient(135deg,#5d7485,#c9d3da 50%,#3f4a52)"></div><div class="title">There are many variations passages Lorem Ipsum</div><div class="text">If you use this site regularly and would like to help keep the site on the Internet, please consider donating a small sum to help pay</div><div class="btn">Read More <span class="dot"><svg width="8" height="8" viewBox="0 0 8 8"><path d="M3 1l3 3-3 3" fill="none" stroke="#222" stroke-width="1.5"/></svg></span></div></div>
<div class="news" style="left:783px;top:3098px"><div class="pic" role="img" aria-label="Engineers overlooking a building site" style="background:linear-gradient(180deg,#e6ebef,#b7c0c6 50%,#7b7f72)"></div><div class="title">There are many variations passages Lorem Ipsum</div><div class="text">If you use this site regularly and would like to help keep the site on the Internet, please consider donating a small sum to help pay</div><div class="btn">Read More <span class="dot"><svg width="8" height="8" viewBox="0 0 8 8"><path d="M3 1l3 3-3 3" fill="none" stroke="#222" stroke-width="1.5"/></svg></span></div></div>

<!-- GALLERY -->
<div class="photo" role="img" aria-label="Offshore platform at sunset" style="left:0;top:3543px;width:240px;height:177px;background:linear-gradient(180deg,#e6a060,#a7705a 50%,#3b4a5d)"></div>
<div class="photo" role="img" aria-label="Yellow excavator in a snowy forest" style="left:240px;top:3543px;width:240px;height:177px;background:linear-gradient(135deg,#7d97a6,#4f6470 50%,#c9b23c)"></div>
<div class="photo" role="img" aria-label="Aerial view of an industrial complex" style="left:480px;top:3543px;width:240px;height:177px;background:linear-gradient(135deg,#a9aca8,#70746f 60%,#d1d3cf)"></div>
<div class="photo" role="img" aria-label="Tower crane over a building site" style="left:720px;top:3543px;width:240px;height:177px;background:linear-gradient(180deg,#3f86d6,#8cbbe8 60%,#8a5b3c)"></div>
<div class="photo" role="img" aria-label="Workers in hard hats" style="left:960px;top:3543px;width:240px;height:177px;background:linear-gradient(180deg,#9ba3a8,#5c6166 50%,#2e3235)"></div>
<div class="photo" role="img" aria-label="Traveller in an airport terminal" style="left:0;top:3720px;width:240px;height:176px;background:linear-gradient(135deg,#e9e3cf,#9aa394 50%,#3c4046)"></div>
<div class="photo" role="img" aria-label="Excavator on a construction site" style="left:240px;top:3720px;width:240px;height:176px;background:linear-gradient(180deg,#4f8ccc,#9cc0e0 55%,#c98a52)"></div>
<div class="photo" role="img" aria-label="Rows of lettuce in a greenhouse" style="left:480px;top:3720px;width:240px;height:176px;background:linear-gradient(180deg,#e5e8e2,#8fc45a 55%,#4f8a2e)"></div>
<div class="photo" role="img" aria-label="Offshore rig seen from above" style="left:720px;top:3720px;width:240px;height:176px;background:linear-gradient(135deg,#2f6a78,#4a8a93 50%,#1f4d5a)"></div>
<div class="photo" role="img" aria-label="Gas refinery towers" style="left:960px;top:3720px;width:240px;height:176px;background:linear-gradient(180deg,#2f6fd0,#6e9ee0 50%,#3b3b3b)"></div>

<!-- FOOTER -->
<div class="f-head" style="left:93px">Quick Links</div>
<ul class="f-list" style="left:93px;top:4020px"><li>Home</li><li>About Us</li><li>Services</li><li>News</li><li>Contact Us</li></ul>
<div class="f-head" style="left:259px">Services</div>
<ul class="f-list" style="left:259px;top:4020px"><li>Construction</li><li>Oil Industry</li><li>Enegy &amp; gas services</li><li>Agricultural Projects</li></ul>
<ul class="f-list" style="left:410px;top:4020px"><li>Real Estate Development</li><li>Travel &amp; Tourism</li><li>Food Processing</li><li>Human Sources Services</li></ul>
<div class="f-head" style="left:634px">Contact Us</div>
<div class="contact" style="top:4018px"><svg width="10" height="14" viewBox="0 0 10 14"><path d="M5 0a5 5 0 0 0-5 5c0 4 5 9 5 9s5-5 5-9a5 5 0 0 0-5-5zm0 7a2 2 0 1 1 0-4 2 2 0 0 1 0 4z" fill="#f7901e"/></svg><span>42 Harbour Row<br>Westbrook 4100</span></div>
<div class="contact" style="top:4068px"><svg width="12" height="12" viewBox="0 0 12 12"><path d="M2.5 0.5l2 2.5-1.2 1.5a7 7 0 0 0 4.2 4.2L9 7.5l2.5 2-1.2 2C5 11.5 0.5 7 0.5 1.7z" fill="#f7901e"/></svg><span>+1 (555) 014 2290</span></div>
<div class="contact" style="top:4110px"><svg width="12" height="10" viewBox="0 0 12 10"><rect width="12" height="10" fill="#f7901e"/><path d="M0 0l6 5 6-5" fill="none" stroke="#fff" stroke-width="1"/></svg><span>info@kvrglobalinks.com</span></div>
<div class="f-head" style="left:863px">Newsletter</div>
<div class="input" style="top:4022px">Enter Name:</div>
<div class="input" style="top:4057px">Enter Email:</div>
<div class="subscribe">Subscribe</div>

<div class="copyright">COPYRIGHT © 2020 <b>KVR GLOBALINKS</b>. ALL RIGHTS RESERVED.</div>
<div class="f-social"><span class="on"></span><span></span><span></span><span></span></div>

</body>
</html>
```